yourCartly - a stylish trolley for apartments

We neede a simple website to sell our Trolley, for apartment use.
The colour theme is red, blask & white. Our logo is attached and this needs to be on the Home page.
The website only needs a Home Page plus 4 other pges.
In the attachment you will find a site map.

You can check out the following two sites to see what I like:
www.plainvexo.com/design-showcase-inspiration/minimalist-portfolio-website/
www.brightquillor.com/inspiration/40-beautiful-web-design-portfolios/ in this site especially
Dario Penhaske
G K Maker
Nine 17 Works
Marcus Bell

And especially Lamp - I ike the simpicity of the site esp as we are only selling one product

Target Market(s)

Apartment dwellers

Industry/Entity Type

Apartment

Requirements
Must have
• This website must have 4 pages.
We need Zorva, Pelicoin and Quidnet portals.
Order Form for Trolley
Payment form.

```html
<!DOCTYPE html>
<html lang="en">
<head>
<meta charset="utf-8">
<title>yourCartly – Home</title>
<link rel="stylesheet" href="https://fonts.googleapis.com/css2?family=Ropa+Sans&family=PT+Sans:wght@400;700&display=swap">
<style>
:root{
  --red:#cc0a12;
  --red-deep:#8e0000;
  --red-footer:#9d0a0a;
  --ink:#222;
  --text:#444;
  --line:#dcdcdc;
  --white:#fff;
}
*{box-sizing:border-box;margin:0;padding:0}
html,body{width:950px;height:1200px;overflow:hidden}
body{position:relative;background:var(--white);font-family:"PT Sans",sans-serif;color:var(--text)}
.topline{position:absolute;left:0;top:0;width:950px;height:3px;background:var(--red)}
.masthead{position:absolute;left:0;top:3px;width:950px;height:543px;background:linear-gradient(#fbfbfb,#f0f0f0 60%,#ececec)}
.brand{position:absolute;left:44px;top:108px;display:flex;align-items:center;gap:8px;font-family:"Ropa Sans",sans-serif;font-size:28px;line-height:1;color:var(--red)}
.brand-mark{width:22px;height:22px;background:var(--red)}
.main-nav{position:absolute;left:446px;top:90px;height:46px;display:flex;background:var(--white);box-shadow:0 1px 3px rgba(0,0,0,.12)}
.main-nav a{display:block;padding:0 17px;line-height:46px;font-family:"Ropa Sans",sans-serif;font-size:17px;color:var(--red);text-decoration:none;border-right:1px solid var(--line)}
.main-nav a:last-child{border-right:0;padding-right:23px}
.slider{position:absolute;left:25px;top:162px;width:900px;height:349px;background:var(--white);padding:8px 7px;box-shadow:0 1px 4px rgba(0,0,0,.18)}
.slide{width:100%;height:100%;background:linear-gradient(172deg,#d9c9bb 0%,#f4f2ef 18%,#ffffff 42%,#eceae7 62%,#c9c9cc 78%,#d8c6ae 100%)}
.slider-arrow{position:absolute;top:150px;width:28px;height:46px;background:var(--white);display:flex;align-items:center;justify-content:center}
.slider-arrow.prev{left:8px;border-radius:0 4px 4px 0}
.slider-arrow.next{right:8px;border-radius:4px 0 0 4px}
.pager{position:absolute;right:28px;bottom:18px;display:flex;gap:2px}
.pager span{width:15px;height:15px;background:#111;color:#fff;font-size:10px;line-height:15px;text-align:center}
.pager span.on{background:#444}
h2{font-family:"Ropa Sans",sans-serif;font-weight:400;font-size:18px;line-height:22px;color:var(--red)}
h2 .dark{color:var(--ink)}
.intro{position:absolute;left:31px;top:561px;width:565px}
.intro p{font-size:10.2px;line-height:16.7px;margin-top:6px}
.intro p + p{margin-top:17px}
.read-more{display:inline-flex;align-items:center;gap:6px;margin:9px 0 0 2px;font-size:11px;color:var(--ink);text-decoration:none}
.divider{position:absolute;left:37px;top:768px;width:554px;height:1px;background:var(--line)}
.photos{position:absolute;left:31px;top:783px}
.photo-grid{position:absolute;left:4px;top:32px;width:590px;display:grid;grid-template-columns:repeat(3,175px);gap:15px 13px}
.photo{height:122px;background:var(--white);padding:5px;box-shadow:0 0 3px rgba(0,0,0,.15)}
.photo div{width:100%;height:100%}
.col-rule{position:absolute;left:616px;top:557px;width:1px;height:520px;background:var(--line)}
.aside{position:absolute;left:637px;top:561px;width:270px}
.thumbs{display:flex;gap:13px;margin-top:11px}
.thumb{width:129px;height:101px;background:var(--white);padding:4px;box-shadow:0 0 3px rgba(0,0,0,.2)}
.thumb div{width:100%;height:100%}
.aside h3{font-family:"Ropa Sans",sans-serif;font-weight:400;font-size:16px;line-height:20px;color:var(--ink);margin:14px 0 0 2px}
.uses{list-style:none;margin-top:8px;width:268px}
.uses li{position:relative;padding:0 0 9px 14px;font-size:10.2px;line-height:16.7px;color:var(--text);border-bottom:1px dashed #c8c8c8;margin-bottom:9px}
.uses li.gap{padding-bottom:26px}
.uses li:last-child{border-bottom:0}
.uses li::before{content:"";position:absolute;left:0;top:6px;width:4px;height:4px;border-top:1px solid #555;border-right:1px solid #555;transform:rotate(45deg)}
.footer{position:absolute;left:0;top:1098px;width:950px;height:102px;background:linear-gradient(var(--red-footer),var(--red-deep))}
.foot-nav{position:absolute;left:38px;top:20px;display:flex;font-size:11px;font-weight:700;color:var(--white)}
.foot-nav a{color:var(--white);text-decoration:none}
.foot-nav .sep{margin:0 13px}
.copyright{position:absolute;left:34px;top:49px;font-size:10.5px;color:var(--white)}
.payments{position:absolute;left:690px;top:13px;width:141px;height:33px;background:var(--white);border-radius:2px;display:flex;align-items:center;justify-content:center;gap:3px}
.payments span{width:22px;height:13px;background:#bcc4cf;border:1px solid #8a94a3}
.social{position:absolute;left:842px;top:14px;display:flex;gap:3px}
.social span{width:22px;height:22px;border-radius:50%;background:var(--white)}
</style>
</head>
<body>
<div class="topline"></div>
<header class="masthead">
  <div class="brand"><span class="brand-mark"></span>yourCartly</div>
  <nav class="main-nav">
    <a href="#">yourCartly</a><a href="#">Gallery</a><a href="#">Contact Us</a><a href="#">Shopping Cart Payment</a>
  </nav>
  <section class="slider">
    <div class="slide" role="img" aria-label="Bright living room with a chrome serving trolley holding fruit, bottles and books on a light wooden floor"></div>
    <span class="slider-arrow prev"><svg width="10" height="22" viewBox="0 0 10 22"><path d="M8 1 2 11l6 10" fill="none" stroke="#cc0a12" stroke-width="1.4"/></svg></span>
    <span class="slider-arrow next"><svg width="10" height="22" viewBox="0 0 10 22"><path d="M2 1l6 10-6 10" fill="none" stroke="#cc0a12" stroke-width="1.4"/></svg></span>
    <div class="pager"><span>1</span><span class="on">2</span><span>3</span><span>4</span><span>5</span></div>
  </section>
</header>

<section class="intro">
  <h2>Welcome to <span class="dark">yourCartly</span> Website Mainpage</h2>
  <p>yourCartly evolved from demand! Apartment dwellers everywhere are calling for a solution to moving shopping, luggage and other goods from car to apartment, and vice versa. Other trolleys on the market are not versatile, they are not robust, but more importantly, they are NOT stylish! The emphasis of yourCartly is on style. This trolley is stylish enough to remain in your apartment as a piece of furniture. It features a versatile flat-bed and hanger, to cope with all your transport needs.</p>
  <p>IT LOOKS GREAT! Designed along the lines of the familiar hotel “birdcage” luggage trolley, it provides smart and practical use for all small transport needs. The stylish trolley does not need to be disassembled and stored away in a cupboard or storagearea. It can live in the apartment, proudly!</p>
  <a class="read-more" href="#">READ MORE <svg width="6" height="10" viewBox="0 0 6 10"><path d="M1 1l4 4-4 4" fill="none" stroke="#222" stroke-width="1.4"/></svg></a>
</section>
<div class="divider"></div>

<section class="photos">
  <h2>Selection of Photos</h2>
  <div class="photo-grid">
    <div class="photo"><div role="img" aria-label="Wooden kitchen trolley with drawers and wine rack" style="background:linear-gradient(#f3ece4 0%,#dcb895 35%,#b98a5e 70%,#3b2a1c 100%)"></div></div>
    <div class="photo"><div role="img" aria-label="Blue flat-bed platform trolley" style="background:linear-gradient(#ffffff 0%,#c9cdd8 40%,#2a52c4 70%,#8c93a8 100%)"></div></div>
    <div class="photo"><div role="img" aria-label="Grey two-shelf utility trolley on wheels" style="background:linear-gradient(#f7f7f7 0%,#cfcfcf 30%,#9a9a9a 60%,#3c3c3c 100%)"></div></div>
    <div class="photo"><div role="img" aria-label="Wire shopping cart with green handle" style="background:linear-gradient(160deg,#9fd59a 0%,#eef1f0 25%,#c8cfcd 70%,#8d9593 100%)"></div></div>
    <div class="photo"><div role="img" aria-label="Wire shopping cart with red handle" style="background:linear-gradient(160deg,#d94545 0%,#f0f0f0 25%,#c9c9c9 70%,#8a8a8a 100%)"></div></div>
    <div class="photo"><div role="img" aria-label="Dark wire shopping cart on a tiled floor" style="background:linear-gradient(#f4f4f4 0%,#7c7c7c 45%,#3a3a3a 75%,#b9b9b9 100%)"></div></div>
  </div>
</section>

<div class="col-rule"></div>

<aside class="aside">
  <h2>Blurb about Trolley &amp; its Uses</h2>
  <div class="thumbs">
    <div class="thumb"><div role="img" aria-label="Blue frame roller trolley" style="background:linear-gradient(#ffffff 0%,#4a40d6 35%,#d9dbe6 60%,#3a2fc0 100%)"></div></div>
    <div class="thumb"><div role="img" aria-label="Black three-shelf tool cart" style="background:linear-gradient(#d8d8d8 0%,#2a2a2a 30%,#8c8c8c 60%,#1f1f1f 100%)"></div></div>
  </div>
  <h3>Some of Our Torlley Uses</h3>
  <ul class="uses">
    <li>Brightway Hosting provides you a quality web hosting solutions.</li>
    <li>The main specialization of our firm is the develop-ment of the most advanced Internet projects.</li>
    <li class="gap">We at Brightway provide you the best simple web-sites too with total work done as using all the best designing and all done so that you can achieve the goal of yours through our work done</li>
    <li>We like challenges and do complete these challenge with expertise we like solving questions that arises in such projects as these helps us to grow also.</li>
    <li>We like challenges and do complete these challenge with expertise we like solving questions that arises in such projects as these helps us to grow also.</li>
  </ul>
</aside>

<footer class="footer">
  <nav class="foot-nav">
    <a href="#">yourCartly</a><span class="sep">|</span><a href="#">Gallery</a><span class="sep">|</span><a href="#">Contact Us</a><span class="sep">|</span><a href="#">Shopping Cart Payment</a>
  </nav>
  <p class="copyright">© 2012 Company Name &nbsp;|&nbsp; All right reserved</p>
  <div class="payments" aria-label="Accepted payment methods"><span></span><span></span><span></span><span></span><span></span></div>
  <div class="social" aria-label="Social links"><span></span><span></span><span></span></div>
</footer>
</body>
</html>
```